Business Card - Tidal Lanes

Need Business Card design for company named Tidal Lanes. Software development focused mainly on Brindle Orvix & Zelt Apps. I've attached our logo with both a black and white background. Please add trademark symbol to logo when using.

```html
<!DOCTYPE html>
<html lang="en">
<head>
<meta charset="utf-8">
<title>Tidal Lanes – Business Card</title>
<link rel="stylesheet" href="https://fonts.googleapis.com/css2?family=Ubuntu:wght@400;500;700&display=swap">
<style>
  :root {
    --bg: #e9e6e1;
    --card-black: #060606;
    --brand-red: #d8202a;
    --brand-orange: #f39a1e;
    --brand-yellow: #f8c21a;
    --name-red: #c3161f;
    --ink-dark: #2a1a08;
    --white: #ffffff;
    --muted: #d9d9d9;
  }
  * { box-sizing: border-box; margin: 0; padding: 0; }
  html, body {
    width: 1200px; height: 720px; overflow: hidden;
    background: var(--bg);
    font-family: "Ubuntu", "Helvetica Neue", Arial, sans-serif;
  }
  .sheet {
    width: 1200px; height: 720px;
    display: flex; align-items: center; justify-content: center; gap: 40px;
  }
  .card {
    width: 540px; height: 309px;
    position: relative; overflow: hidden;
    background: var(--card-black);
    box-shadow: 0 6px 18px rgba(0,0,0,0.18);
  }

  /* Front */
  .front__brand {
    position: absolute; left: 0; right: 0; top: 0; height: 160px;
    display: flex; align-items: center; justify-content: center;
  }
  .wordmark {
    color: var(--white); font-weight: 700; letter-spacing: -0.5px;
    display: flex; align-items: center; gap: 10px;
  }
  .wordmark__dot {
    width: 14px; height: 14px; border-radius: 50%;
    background: var(--brand-orange);
  }
  .front .wordmark { font-size: 34px; }
  .band-red-top {
    position: absolute; left: 0; right: 0; top: 160px; height: 16px;
    background: var(--brand-red);
  }
  .band-info {
    position: absolute; left: 0; right: 0; top: 176px; height: 78px;
    background: linear-gradient(90deg, var(--brand-yellow) 0%, var(--brand-orange) 100%);
    display: flex; flex-direction: column; align-items: center; justify-content: center; gap: 8px;
  }
  .person { color: var(--name-red); font-size: 19px; font-weight: 700; }
  .person__title { font-weight: 400; font-size: 15px; }
  .phones {
    display: flex; gap: 26px; color: var(--ink-dark); font-size: 15px;
  }
  .phones__item { display: flex; align-items: center; gap: 6px; }
  .phones__icon { width: 13px; height: 16px; }
  .band-red-bottom {
    position: absolute; left: 0; right: 0; top: 254px; height: 6px;
    background: var(--brand-red);
  }
  .band-address {
    position: absolute; left: 0; right: 0; top: 260px; bottom: 0;
    background: var(--brand-yellow);
    display: flex; align-items: center; justify-content: center;
    color: var(--ink-dark); font-size: 14px;
  }

  /* Back */
  .back { display: flex; align-items: center; justify-content: center; }
  .back .wordmark { font-size: 58px; }
  .back .wordmark__dot { width: 20px; height: 20px; }
  .back__web {
    position: absolute; left: 0; right: 0; bottom: 44px;
    text-align: center; color: var(--muted); font-size: 15px; letter-spacing: 0.5px;
  }
</style>
</head>
<body>
<main class="sheet">
  <section class="card front" aria-label="Card front">
    <div class="front__brand">
      <div class="wordmark"><span class="wordmark__dot"></span>Tidal Lanes™</div>
    </div>
    <div class="band-red-top"></div>
    <div class="band-info">
      <p class="person">Your Name, <span class="person__title">Title</span></p>
      <div class="phones">
        <span class="phones__item">
          <svg class="phones__icon" viewBox="0 0 13 16" aria-hidden="true">
            <rect x="2" y="1" width="9" height="14" rx="1.5" fill="var(--ink-dark)"/>
            <rect x="3.5" y="3" width="6" height="6" fill="var(--brand-yellow)"/>
          </svg>555-207-4410
        </span>
        <span class="phones__item">
          <svg class="phones__icon" viewBox="0 0 16 16" aria-hidden="true" style="width:16px">
            <path d="M3 7 L5 3 H11 L13 7 Z" fill="var(--ink-dark)"/>
            <rect x="1.5" y="7" width="13" height="5" rx="1" fill="var(--ink-dark)"/>
            <circle cx="4.5" cy="13" r="1.6" fill="var(--ink-dark)"/>
            <circle cx="11.5" cy="13" r="1.6" fill="var(--ink-dark)"/>
          </svg>555-318-6625
        </span>
      </div>
    </div>
    <div class="band-red-bottom"></div>
    <div class="band-address">2410 Harbor Row, Marlow, FL 30917</div>
  </section>

  <section class="card back" aria-label="Card back">
    <div class="wordmark"><span class="wordmark__dot"></span>Tidal Lanes™</div>
    <p class="back__web">www.tidallanes.com</p>
  </section>
</main>
</body>
</html>
```